Emergency and Referral Vet Hospital promotional sticker design

We're looking at getting some stickers designed that we could give to clients to put on their cars for promotion and advertising. If they could also be suitable for a goodie bag for conference too that would be great. I like the look of water-colour backgrounds, we'll need to include our logo and probably our address (Unit 3/215 Korrinup Road Tallowmere). We also have a hospital motto "... because they're family" if that could somehow be integrated, we only care for small animals (dogs, cats etc) but the design is very open to suggestion. Would love to see what you can create.

Industry/Entity Type

Veterinary

Colors
0054AA
0677BA
7BADD7
CADEEF
E8F1F8
0094D4
00A9DD
6FCCEA
C7EBF8
E9F6FB

Requirements
Nice to have
• Think beach vibes, blues maybe paw print shapes etc

```html
<!DOCTYPE html>
<html lang="en">
<head>
<meta charset="utf-8">
<title>Tidewell Veterinary – Comprehensive Veterinary Care</title>
<link rel="stylesheet" href="https://fonts.googleapis.com/css2?family=Outfit:wght@500;600&family=Great+Vibes&display=swap">
<style>
  :root {
    --ink: #111418;
    --navy: #0054AA;
    --ocean: #0677BA;
    --sky: #7BADD7;
    --mist: #CADEEF;
    --foam: #E8F1F8;
    --white: #ffffff;
  }
  html, body {
    margin: 0;
    padding: 0;
    overflow: hidden;
    background: var(--white);
  }
  .poster {
    position: relative;
    width: 1200px;
    height: 800px;
    overflow: hidden;
    background: linear-gradient(180deg, #ffffff 0%, #fbfdff 100%);
    font-family: "Outfit", sans-serif;
  }
  .brand {
    position: absolute;
    left: 50px;
    top: 150px;
    display: flex;
    align-items: center;
    gap: 10px;
    font-family: "Outfit", sans-serif;
    font-weight: 600;
    font-size: 34px;
    color: var(--ink);
    letter-spacing: 1px;
  }
  .brand-dot {
    width: 14px;
    height: 14px;
    border-radius: 50%;
    background: var(--ocean);
  }
  .headline {
    position: absolute;
    left: 50px;
    top: 258px;
    margin: 0;
    font-weight: 600;
    font-size: 53px;
    line-height: 73px;
    color: var(--ink);
  }
  .headline .accent {
    color: var(--navy);
  }
  .motto {
    position: absolute;
    left: 20px;
    top: 500px;
    margin: 0;
    font-family: "Great Vibes", cursive;
    font-size: 64px;
    color: var(--ink);
    white-space: nowrap;
  }
  .motto .accent {
    color: var(--navy);
  }
  .address-band {
    position: absolute;
    left: 0;
    top: 627px;
    width: 640px;
    height: 130px;
    background: linear-gradient(90deg, var(--ocean) 0%, #1a86c6 60%, rgba(123,173,215,0.6) 100%);
  }
  .pin-icon {
    position: absolute;
    left: 60px;
    top: 28px;
    width: 74px;
    height: 74px;
  }
  .address {
    position: absolute;
    left: 149px;
    top: 32px;
    margin: 0;
    font-style: normal;
    font-weight: 500;
    font-size: 27px;
    line-height: 34px;
    color: var(--white);
  }
  .photo {
    position: absolute;
    left: 0;
    top: 0;
    width: 1200px;
    height: 800px;
    pointer-events: none;
  }
</style>
</head>
<body>
<main class="poster">

  <div class="brand">
    <span class="brand-dot"></span>
    <span class="brand-name">tidewell</span>
  </div>

  <h1 class="headline">
    Comprehensive<br>
    <span class="accent">Veterinary care</span><br>
    for your pets
  </h1>

  <p class="motto">… Because <span class="accent">they’re family</span></p>

  <div class="address-band">
    <svg class="pin-icon" viewBox="0 0 74 74" aria-hidden="true">
      <circle cx="37" cy="37" r="34" fill="none" stroke="#ffffff" stroke-width="3"/>
      <path d="M37 17c-8 0-14 6-14 14 0 10 14 26 14 26s14-16 14-26c0-8-6-14-14-14z" fill="#ffffff"/>
      <circle cx="37" cy="31" r="5.5" fill="#0677BA"/>
    </svg>
    <address class="address">Unit 3/215 Korrinup Road<br>Tallowmere</address>
  </div>

  <svg class="photo" viewBox="0 0 1200 800">
    <defs>
      <linearGradient id="clinicTone" x1="0" y1="0" x2="1" y2="1">
        <stop offset="0" stop-color="#d9dde0"/>
        <stop offset="0.45" stop-color="#b9c6d2"/>
        <stop offset="0.7" stop-color="#d9a46e"/>
        <stop offset="1" stop-color="#8a8f96"/>
      </linearGradient>
    </defs>
    <path role="img" aria-label="Veterinarian in a mask and white coat examining a smiling corgi on a clinic table"
      d="M540 300 C560 200 620 110 720 60 C820 20 960 20 1040 50 C1110 80 1160 160 1200 230 L1200 640 C1120 680 1000 740 880 765 C760 785 620 760 560 700 C520 640 505 560 510 460 C515 400 525 350 540 300 Z"
      fill="url(#clinicTone)"/>
    <path d="M555 680 C620 760 760 790 880 768 C1000 746 1120 690 1200 640"
      fill="none" stroke="#0054AA" stroke-width="8" stroke-linecap="round"/>
  </svg>

</main>
</body>
</html>
```